Redo a PPT pres. - Real Estate in Brazil - Socially equitable investments in Social Housing

We need to redo the presentation attached. It is an institutional presentation to attract local and foreign investors to invest in Brazilian Social Housing Projects structured by our company "TLR".
A middle class of 100 million, a housing deficit of 9M, a strong political will & positive income generation trends constitute grounds for a significant demand in social housing.
This make a perfect scheme for investors to invest in Brazilian Social Housing.
"TLR", is a consulting "boutique" focused in Brazilian real estate, specialized in structuring, analyzing and originating Brazilian social housing projects.
TLR is part of the group TLB. TLB is structured to create value through each step of the residential real estate business - structuring, financing, sales, marketing and technology.
We would like to see designs that use mainly the color blue. The final design should communicate financial safety and professionalism. In order to reach our needs, the designer will need to have basic understanding of finance and investment in order to highlight the most important information.
The idea is to receive back the PPT with each page redesigned and an homogeneous identity.
To all designers,
Target Market(s)
Institutional Investors and wealthy individuals
Industry/Entity Type
Residential
Look and feel

```html
<!DOCTYPE html>
<html lang="en">
<head>
<meta charset="utf-8">
<title>The Time Is Now – Social Housing in Brazil</title>
<link href="https://fonts.googleapis.com/css2?family=Carlito:wght@400;700&family=Libre+Baskerville:wght@700&display=swap" rel="stylesheet">
<style>
  :root {
    --navy: #0b2a63;
    --navy-deep: #061c4a;
    --navy-mid: #1a4a95;
    --sky: #4aa8ec;
    --accent-line: #7fc8f5;
    --label-blue: #2f7ad6;
    --ink: #262a30;
    --sub-ink: #3b3f46;
    --body-light: #f4f8fd;
    --body-tint: #dbe7f5;
    --white: #ffffff;
  }
  * { margin: 0; padding: 0; box-sizing: border-box; }
  html, body { width: 1200px; height: 900px; overflow: hidden; background: var(--white); }
  .slide {
    position: relative;
    width: 1200px;
    height: 900px;
    overflow: hidden;
    font-family: "Carlito", "Calibri", Arial, sans-serif;
    background: linear-gradient(180deg, var(--body-light) 0%, var(--body-tint) 100%);
  }
  .backdrop-photo {
    position: absolute;
    left: 0; top: 132px;
    width: 1200px; height: 640px;
    background:
      linear-gradient(90deg, rgba(200,216,236,0.55) 0%, rgba(240,245,252,0.2) 45%, rgba(210,224,242,0.45) 100%);
  }
  .header {
    position: absolute;
    left: 0; top: 0;
    width: 1200px; height: 132px;
    background: linear-gradient(180deg, #0d3070 0%, var(--navy) 100%);
  }
  .header-photo {
    position: absolute;
    right: 0; top: 0;
    width: 380px; height: 132px;
    background: linear-gradient(90deg, rgba(13,48,112,0) 0%, #2b5fa8 45%, #5f8fcb 80%, #3b6db2 100%);
  }
  .header-rule {
    position: absolute;
    left: 0; top: 128px;
    width: 1200px; height: 8px;
    background: linear-gradient(90deg, var(--navy-mid) 0%, #4d86cf 60%, #9cc3ea 100%);
  }
  .title {
    position: absolute;
    left: 27px; top: 54px;
    font-family: "Libre Baskerville", Georgia, serif;
    font-weight: 700;
    font-size: 26px;
    letter-spacing: 0.5px;
    color: var(--white);
  }
  .subtitle-band {
    position: absolute;
    left: 0; top: 150px;
    width: 760px; height: 56px;
    background: linear-gradient(90deg, rgba(255,255,255,0.95) 0%, rgba(255,255,255,0.6) 70%, rgba(255,255,255,0) 100%);
    border-bottom: 2px solid rgba(180,200,225,0.5);
  }
  .subtitle {
    position: absolute;
    left: 28px; top: 158px;
    font-size: 32px;
    font-weight: 700;
    color: var(--sub-ink);
  }
  .agenda {
    position: absolute;
    left: 38px; top: 244px;
    list-style: none;
  }
  .agenda-item {
    display: flex;
    align-items: center;
    height: 57px;
    font-size: 23px;
    font-weight: 700;
    color: var(--ink);
  }
  .agenda-item svg { width: 30px; height: 28px; margin-right: 18px; flex: none; }
  .agenda-label { color: var(--label-blue); margin-right: 6px; }
  .footer-art { position: absolute; left: 0; top: 0; width: 1200px; height: 900px; }
  .brand {
    position: absolute;
    left: 30px; top: 782px;
    display: flex;
    align-items: center;
    gap: 12px;
    color: var(--white);
    font-size: 68px;
    font-weight: 400;
    line-height: 1;
  }
  .brand-mark { width: 22px; height: 22px; background: var(--white); }
  .page-number {
    position: absolute;
    left: 1111px; top: 744px;
    width: 52px; height: 52px;
    border-radius: 50%;
    border: 3px solid #9fc7ee;
    background: var(--navy-deep);
    color: var(--white);
    font-size: 24px;
    font-weight: 700;
    display: flex; align-items: center; justify-content: center;
  }
  .deck-title {
    position: absolute;
    right: 30px; top: 820px;
    font-size: 47px;
    font-weight: 700;
    letter-spacing: 0.5px;
    color: var(--sky);
  }
</style>
</head>
<body>
<div class="slide">
  <div class="backdrop-photo" role="img" aria-label="Faint photo of modern glass office towers"></div>

  <header class="header">
    <div class="header-photo" role="img" aria-label="Photo of glass skyscrapers against the sky"></div>
    <h1 class="title">THE TIME IS NOW!</h1>
  </header>
  <div class="header-rule"></div>

  <div class="subtitle-band"></div>
  <h2 class="subtitle">Add Sub text here</h2>

  <ul class="agenda">
    <li class="agenda-item"><svg viewBox="0 0 30 28"><path d="M2 15 L11 25 L28 3 L24 2 L11 18 L6 12 Z" fill="#0b2a63"/></svg><span class="agenda-label">Macro-environment &amp; Mortgage market:</span> Green Light</li>
    <li class="agenda-item"><svg viewBox="0 0 30 28"><path d="M2 15 L11 25 L28 3 L24 2 L11 18 L6 12 Z" fill="#0b2a63"/></svg><span class="agenda-label">A sophisticated &amp; successful program:</span> Catalyst</li>
    <li class="agenda-item"><svg viewBox="0 0 30 28"><path d="M2 15 L11 25 L28 3 L24 2 L11 18 L6 12 Z" fill="#0b2a63"/></svg><span class="agenda-label">Investment Structure of a typical project:</span> Leverage &amp; Limited Risks</li>
    <li class="agenda-item"><svg viewBox="0 0 30 28"><path d="M2 15 L11 25 L28 3 L24 2 L11 18 L6 12 Z" fill="#0b2a63"/></svg><span class="agenda-label">Small &amp; mid size developers:</span> A partner by choice</li>
    <li class="agenda-item"><svg viewBox="0 0 30 28"><path d="M2 15 L11 25 L28 3 L24 2 L11 18 L6 12 Z" fill="#0b2a63"/></svg><span class="agenda-label">TLR:</span> Value added &amp; Risk mitigation</li>
    <li class="agenda-item"><svg viewBox="0 0 30 28"><path d="M2 15 L11 25 L28 3 L24 2 L11 18 L6 12 Z" fill="#0b2a63"/></svg><span class="agenda-label">TLB:</span> TLR, part of an integrated family of companies</li>
    <li class="agenda-item"><svg viewBox="0 0 30 28"><path d="M2 15 L11 25 L28 3 L24 2 L11 18 L6 12 Z" fill="#0b2a63"/></svg><span class="agenda-label">Appendix:</span> Next step…TLR Fund (2013)</li>
  </ul>

  <svg class="footer-art" viewBox="0 0 1200 900" aria-hidden="true">
    <defs>
      <linearGradient id="footerFill" x1="0" y1="0" x2="0" y2="1">
        <stop offset="0" stop-color="#0d2f6c"/>
        <stop offset="1" stop-color="#061c4a"/>
      </linearGradient>
    </defs>
    <path d="M0 668 C300 770 520 800 700 790 C900 778 1060 720 1200 650 L1200 900 L0 900 Z" fill="url(#footerFill)"/>
    <path d="M0 668 C300 770 520 800 700 790 C900 778 1060 720 1200 650" fill="none" stroke="#7fc8f5" stroke-width="3"/>
  </svg>

  <div class="brand"><span class="brand-mark"></span>TLR</div>
  <div class="page-number">02</div>
  <div class="deck-title">SOCIAL HOUSING IN BRAZIL</div>
</div>
</body>
</html>
```